A New and modern Business Card for Tarwick Trade Solutions Ltd

New and modern Logo and Business Card Attached is the current logo/business card designCurrently the business is called "Tarwick & Co." or TTS Ltd for short. This is subject to change.This business specialises in Telecoms and Energy. We work with the major networks (QV, K7, etc) and also offer Energy Products saving clients money off their energy bills.These are business to business services.The current design incorporates a Pheonix, indicating rebirth, starting something new.We would like to maintain the Phoenix element but a newer modern style.We love colours in the logo 3 max.The aim of this is to be ultra slick and modern. I envisage Tarwick & Co. on one side of the card with long descriptions on the other side.Side 1:TTS Ltd/Logo?Side 2:TTS Ltd/Logo/Graphic?Brogan & Co.Name:Address:Phone:Email:The design is mostly flexible but must incorporate a Phoenix.For example "Tarwick & Co." with a block phoenix behind the text...up to you.

Industry/Entity Type

Telecommunications

Contact Information for Business Card

Tarwick & Co.
Address:
Name:
Phone:
Email:

Logo Text

Tarwick & Co.

Colors
33a6d7
0792cd
acd037
9bcb3c
f78f20
fece3e

Requirements
Must have
• Phoenix
• 3/4 colours max
• Blue representing Technology (wireless)
• Green for Eco Energy
• Orange for Phoenix
• White business card background
Should not have
• phoenix must not all be red/ orange fire, we are a technology service company and the phoenix colours must represent this. Fire is not representative of our company.

```html
<!DOCTYPE html>
<html lang="en">
<head>
<meta charset="utf-8">
<title>Tarwick Trade Solutions Ltd – Business Card</title>
<link rel="stylesheet" href="https://fonts.googleapis.com/css2?family=Cinzel:wght@600&family=Lato:wght@400;700&display=swap">
<style>
  :root {
    --bg: #e9e7e5;
    --card-white: #ffffff;
    --tech-blue: #0792cd;
    --tech-blue-light: #33a6d7;
    --eco-green: #9bcb3c;
    --eco-green-light: #acd037;
    --phoenix-orange: #f78f20;
    --text-grey: #4a4a4a;
    --rule: #dfe6ea;
  }
  * { box-sizing: border-box; margin: 0; padding: 0; }
  html, body { width: 1200px; height: 782px; overflow: hidden; background: var(--bg); }
  .canvas { position: relative; width: 1200px; height: 782px; }

  .card {
    position: absolute;
    width: 560px;
    height: 320px;
    box-shadow: 0 6px 18px rgba(0,0,0,0.18);
  }

  /* Back side */
  .card-back {
    left: 570px;
    top: 60px;
    overflow: hidden;
  }
  .card-back .pattern-fill {
    position: absolute; inset: 0;
    background: linear-gradient(160deg, var(--tech-blue-light) 0%, var(--tech-blue) 55%, #2f9f9a 80%, var(--eco-green) 100%);
  }
  .card-back .back-mark {
    position: absolute;
    right: 70px;
    bottom: 56px;
    display: flex;
    align-items: center;
    gap: 10px;
    font-family: "Cinzel", serif;
    font-weight: 600;
    font-size: 22px;
    letter-spacing: 1px;
    color: #ffffff;
  }
  .back-mark .dot { width: 18px; height: 18px; border-radius: 50%; background: var(--phoenix-orange); }

  /* Front side */
  .card-front {
    left: 70px;
    top: 390px;
    background: var(--card-white);
    display: flex;
    align-items: center;
  }
  .brand-block {
    width: 290px;
    padding-left: 40px;
    display: flex;
    flex-direction: column;
    align-items: flex-start;
  }
  .brand-block .mark-circle {
    width: 56px; height: 56px; border-radius: 50%;
    background: var(--phoenix-orange);
    margin: 0 0 14px 70px;
  }
  .brand-name {
    font-family: "Cinzel", serif;
    font-weight: 600;
    line-height: 1;
  }
  .brand-name .primary { display: block; font-size: 40px; letter-spacing: 1px; color: var(--tech-blue); }
  .brand-name .secondary { display: block; font-size: 11.5px; letter-spacing: 1.2px; margin-top: 6px; color: var(--eco-green); }

  .divider { width: 1px; height: 150px; background: var(--rule); }

  .contact-block {
    padding-left: 28px;
    font-family: "Lato", sans-serif;
    color: var(--text-grey);
    text-transform: uppercase;
    font-size: 14px;
    line-height: 1.3;
    letter-spacing: 0.5px;
  }
  .person-name { color: var(--phoenix-orange); font-weight: 700; font-size: 19px; letter-spacing: 0.6px; }
  .person-title { font-size: 13px; margin-bottom: 6px; }
  .contact-line { display: flex; align-items: center; gap: 7px; }
  .contact-line svg { width: 13px; height: 13px; flex: none; }
  .address { margin-top: 4px; }
</style>
</head>
<body>
<main class="canvas">
  <section class="card card-back" aria-label="Card back">
    <div class="pattern-fill" role="img" aria-label="Blue to green gradient with a faint repeating brand motif pattern"></div>
    <div class="back-mark"><span class="dot"></span>TARWICK</div>
  </section>

  <section class="card card-front" aria-label="Card front">
    <div class="brand-block">
      <span class="mark-circle"></span>
      <div class="brand-name">
        <span class="primary">TARWICK</span>
        <span class="secondary">TRADE SOLUTIONS LIMITED</span>
      </div>
    </div>
    <div class="divider"></div>
    <div class="contact-block">
      <div class="person-name">Daniel Marsh</div>
      <div class="person-title">Managing Director</div>
      <div class="contact-line">
        <svg viewBox="0 0 16 16" aria-hidden="true"><path fill="var(--tech-blue)" d="M4 1.5l2.2 3-1.4 1.6c.9 2 2.6 3.7 4.6 4.6l1.6-1.4 3 2.2-1 2.4C7.6 14.3 1.7 8.4 1.6 3.1z"/></svg>
        <span>044-555 018 274</span>
      </div>
      <div class="contact-line">
        <svg viewBox="0 0 16 16" aria-hidden="true"><rect x="1" y="3" width="14" height="10" fill="var(--tech-blue)"/><path d="M1.5 3.5L8 9l6.5-5.5" fill="none" stroke="#fff" stroke-width="1.2"/></svg>
        <span>info@tarwickmail.com</span>
      </div>
      <div class="address">18 Kestrel Row<br>Ashby Vale, 40217</div>
    </div>
  </section>
</main>
</body>
</html>
```